Business card for marketing analytics company

Need a business card for new company. I have a logo already that I want to be built into the card and should use those colours

Company is called steered by tallies
Design must bring steered by tallies to life not be a card that could be for anyone with a logo put on it.

Like the front to be fairly clean and uncluttered bringing the logo out with a suitable design on the back of the card.

The logo represents a compass and business growth so those themes along with numbers, analytics , data are appropriate.
I'm often working with creative industries so also needs to reflect the creative side of analytics rather than be very corporate looking.

Target Market(s)

Ad agency, media agency, consumer goods clients

Industry/Entity Type

Market Research

Contact Information for Business Card

Needs to include name, title, email and phone number

Colors
f78f20
f68d4d
ec1f27

Requirements
Must have
• Must bring steered by tallies to life not be a card that could be for anyone with a logo put on it.
• Logo, Correct colours
• Like a design on the back that relates to company name
• Designs for both sides
Should not have
• Please do not just submit logo and a coloured card.
• It needs to have a design element to it
• No black background
• No clear cards - needs front & back

```html
<!DOCTYPE html>
<html lang="en">
<head>
<meta charset="utf-8">
<title>Steered by Tallies – Business Card</title>
<link href="https://fonts.googleapis.com/css2?family=Lato:wght@400;700&family=Montserrat:wght@400&display=swap" rel="stylesheet">
<style>
  :root {
    --backdrop: #2f2f2f;
    --paper: #ffffff;
    --brand-red: #c01f26;
    --brand-orange: #f47b20;
    --slate: #4f5b63;
    --ink: #4a4a4a;
    --rule: #c9c9c9;
  }
  * { box-sizing: border-box; margin: 0; padding: 0; }
  html, body {
    width: 1200px;
    height: 987px;
    overflow: hidden;
    background: var(--backdrop);
    font-family: "Lato", sans-serif;
  }
  .card {
    position: absolute;
    left: 293px;
    width: 615px;
    height: 352px;
    border-radius: 16px;
    overflow: hidden;
  }
  .card--front { top: 130px; background: var(--paper); }
  .card--back { top: 505px; background: var(--brand-red); }

  .front-waves { position: absolute; left: 0; top: 0; }

  .brand-lockup {
    position: absolute;
    left: 38px;
    top: 134px;
    display: flex;
    align-items: center;
    gap: 14px;
  }
  .brand-lockup__dot {
    width: 26px;
    height: 26px;
    border-radius: 50%;
    background: var(--brand-orange);
  }
  .brand-lockup__name {
    font-family: "Montserrat", sans-serif;
    font-weight: 400;
    font-size: 23px;
    color: var(--brand-orange);
    line-height: 1;
  }

  .divider {
    position: absolute;
    left: 306px;
    top: 110px;
    width: 1px;
    height: 137px;
    background: var(--rule);
  }

  .contact {
    position: absolute;
    left: 327px;
    top: 112px;
  }
  .contact__name {
    font-size: 23px;
    font-weight: 700;
    color: var(--brand-orange);
    letter-spacing: 0.5px;
    line-height: 1.1;
  }
  .contact__title {
    font-size: 17px;
    font-weight: 700;
    color: var(--brand-red);
    margin-top: 2px;
  }
  .contact__list {
    list-style: none;
    margin-top: 14px;
  }
  .contact__item {
    display: flex;
    align-items: center;
    gap: 8px;
    font-size: 17px;
    color: var(--ink);
    line-height: 24px;
  }
  .contact__icon { width: 14px; height: 14px; flex: none; }

  .back-mark {
    position: absolute;
    left: 318px;
    top: 25px;
    width: 270px;
    height: 270px;
    border: 5px solid var(--paper);
    border-radius: 50%;
  }
  .back-name {
    position: absolute;
    left: 37px;
    top: 218px;
    font-family: "Montserrat", sans-serif;
    font-weight: 400;
    color: var(--paper);
    font-size: 41px;
    line-height: 1.02;
  }
  .back-name__second { display: block; padding-left: 60px; }
  .back-url {
    position: absolute;
    left: 38px;
    top: 306px;
    font-size: 15px;
    letter-spacing: 1.2px;
    color: var(--paper);
  }
</style>
</head>
<body>

<section class="card card--front" aria-label="Card front">
  <svg class="front-waves" width="615" height="352" viewBox="0 0 615 352" aria-hidden="true">
    <path d="M0,301 C90,316 200,318 312,312 C240,322 110,324 0,317 Z" fill="var(--brand-orange)"/>
    <path d="M316,311 C420,296 520,292 615,300 L615,318 C540,305 430,304 316,311 Z" fill="var(--slate)"/>
    <path d="M0,326 C140,338 300,330 420,316 C500,307 560,309 615,322 L615,352 L0,352 Z" fill="var(--brand-red)"/>
  </svg>

  <div class="brand-lockup">
    <span class="brand-lockup__dot"></span>
    <span class="brand-lockup__name">Steered by Tallies</span>
  </div>

  <div class="divider"></div>

  <div class="contact">
    <p class="contact__name">ALAN REEVE</p>
    <p class="contact__title">CEO/Founder</p>
    <ul class="contact__list">
      <li class="contact__item">
        <svg class="contact__icon" viewBox="0 0 24 24" aria-label="Phone"><path fill="var(--brand-orange)" d="M6.6 10.8a15.1 15.1 0 0 0 6.6 6.6l2.2-2.2c.3-.3.7-.4 1-.2 1.1.4 2.3.6 3.6.6.6 0 1 .4 1 1V20c0 .6-.4 1-1 1C10.6 21 3 13.4 3 4c0-.6.4-1 1-1h3.5c.6 0 1 .4 1 1 0 1.3.2 2.5.6 3.6.1.3 0 .7-.2 1z"/></svg>
        555 014 2290
      </li>
      <li class="contact__item">
        <svg class="contact__icon" viewBox="0 0 24 24" aria-label="Email"><path fill="var(--brand-orange)" d="M2 5h20v14H2z"/><path fill="none" stroke="#fff" stroke-width="1.6" d="M2.5 6l9.5 7 9.5-7"/></svg>
        alan@steeredbytally.com
      </li>
      <li class="contact__item">
        <svg class="contact__icon" viewBox="0 0 24 24" aria-label="Website"><circle cx="12" cy="12" r="10" fill="var(--brand-orange)"/><path fill="none" stroke="#fff" stroke-width="1.4" d="M2 12h20M12 2c3 3 3 17 0 20M12 2c-3 3-3 17 0 20"/></svg>
        www.steeredbytally.com
      </li>
    </ul>
  </div>
</section>

<section class="card card--back" aria-label="Card back">
  <div class="back-mark"></div>
  <p class="back-name">Steered by<span class="back-name__second">Tallies</span></p>
  <p class="back-url">www.steeredbytally.com</p>
</section>

</body>
</html>
```